Web Design Project

This is a wordpress project for a newly formed biologics company based in the US with international clientele. We do manufacturing of biologically based raw materials using a state of the art facility....Our logo must be incorporated....logo colors Navy and Gray. It is fine to use some color in web design. The viewer will primarily be industry folk.

Torvell Biologics, LLC is a contract manufacturing organization which produces biologically-based raw materials derived primarily from human plasma. The company services include extraction and purification of plasma components, especially proteins and enzymes. The business focuses on biotherapeutics, diagnostic and veterinary markets worldwide.

5 pages a bad example of first page can be found in attached files.....
use stock photos of labs and clean rooms.
Updates

Project Deadline Extended
Reason: I need a bit more time tonprovide feedback.

Project Deadline Extended
Reason: needed time to evaluate existing options

Target Market(s)

target market Pharmaceutical companies and research universities

Industry/Entity Type

Veterinary

Requirements
Must have
• our logo...we will provide some graphics...

```html
<!DOCTYPE html>
<html lang="en">
<head>
<meta charset="utf-8">
<title>Torvell Biologics, LLC</title>
<link href="https://fonts.googleapis.com/css2?family=Arimo:wght@400&family=Open+Sans:wght@400;700&family=PT+Sans:wght@400;700&display=swap" rel="stylesheet">
<style>
:root{
  --navy:#0d3a73;
  --navy-deep:#1f4c80;
  --nav-blue:#2f5f95;
  --nav-light:#4d83bd;
  --accent-blue:#1565c0;
  --button:#6395cc;
  --gray-text:#8a8a8a;
  --dark-text:#333333;
  --body-text:#555555;
  --sidebar:#efefef;
  --band:#cccccc;
  --header-bg:#f8f8f8;
  --rule:#d9d9d9;
}
*{margin:0;padding:0;box-sizing:border-box}
html,body{width:1059px;height:1200px;overflow:hidden;background:#fff}
.page{position:relative;width:1059px;height:1200px;overflow:hidden;font-family:"Arimo",Arial,sans-serif;color:var(--body-text)}
.abs{position:absolute}
.top-strip{left:0;top:0;width:1059px;height:11px;background:var(--navy-deep)}
.header{left:0;top:11px;width:1059px;height:97px;background:var(--header-bg);border-bottom:1px solid #e6e6e6}
.brand{left:27px;top:22px;display:flex;align-items:center;gap:10px}
.brand-mark{width:78px;height:78px;border-radius:50%;background:var(--navy)}
.brand-name{font-family:"Open Sans",sans-serif;font-weight:700;font-size:27px;color:var(--navy);letter-spacing:-0.5px}
.hero{left:0;top:108px;width:1059px;height:399px;background:linear-gradient(100deg,#eef1f4 0%,#dfe4ea 30%,#f2f4f6 55%,#c9d3de 80%,#e8ecf0 100%)}
.slider-dots{left:979px;top:477px;width:56px;height:20px;border-radius:3px;background:#3a3a3a;display:flex;align-items:center;justify-content:center;gap:8px}
.slider-dots span{width:8px;height:8px;border-radius:50%;background:#8a8a8a}
.slider-dots span.active{background:var(--accent-blue)}
.nav{left:0;top:507px;width:1059px;height:53px;background:radial-gradient(ellipse 420px 60px at 100px 50%,var(--nav-light),transparent 70%),linear-gradient(180deg,var(--nav-blue),#1d4a7e)}
.nav-item{top:0;height:53px;line-height:53px;font-family:"Open Sans",sans-serif;font-size:15px;color:#fff;transform:translateX(-50%);white-space:nowrap}
.nav-sep{top:5px;width:1px;height:43px;background:#1a3f6c;box-shadow:1px 0 0 rgba(255,255,255,0.15)}
.search{left:797px;top:519px;width:231px;height:30px;border:1px solid #5b85b5;background:#24517f;color:#dfe8f2;font-family:"Open Sans",sans-serif;font-size:12px;line-height:28px;padding-left:13px}
.search svg{position:absolute;right:12px;top:6px}
.band{left:0;top:560px;width:1059px;height:14px;background:var(--band)}
.sidebar{left:738px;top:574px;width:295px;height:548px;background:var(--sidebar)}
.welcome-title{left:28px;top:604px;font-family:"PT Sans",sans-serif;font-weight:700;font-size:26px;color:var(--navy);line-height:1}
.welcome-sub{left:29px;top:634px;font-family:"PT Sans",sans-serif;font-weight:700;font-size:18px;color:var(--gray-text);line-height:1}
.text{font-size:12.6px;line-height:19px;color:var(--body-text)}
.welcome-text{left:31px;top:672px;width:676px}
.btn{height:30px;background:var(--button);color:#fff;font-size:13px;line-height:30px;text-align:center;box-shadow:0 1px 2px rgba(0,0,0,0.15)}
.rule-h{height:1px;background:var(--rule)}
.section-title{font-family:"PT Sans",sans-serif;font-weight:700;font-size:19px;color:var(--dark-text);line-height:1}
.section-title span{color:var(--gray-text)}
.services{left:35px;top:912px;list-style:none}
.services li{position:relative;padding-left:15px;height:26.5px;font-size:12.6px;color:var(--body-text)}
.services li::before{content:"";position:absolute;left:0;top:3px;border-left:6px solid #666;border-top:4px solid transparent;border-bottom:4px solid transparent}
.rule-v{left:324px;top:860px;width:1px;height:188px;background:var(--rule)}
.news-date{font-size:12.6px;color:var(--accent-blue)}
.news-text{width:255px}
.staff{left:754px;top:972px;width:265px;height:127px;background:linear-gradient(90deg,#f1f1f1 0%,#e9e6e2 45%,#d9dde2 100%)}
.staff-title{left:14px;top:10px;font-family:"Open Sans",sans-serif;font-weight:700;font-size:28px;line-height:29px;color:#2d2d2d}
.staff-arrow{left:27px;top:72px}
.footer{left:0;top:1122px;width:1059px;height:78px;background:linear-gradient(180deg,#2f5e94,#1f4b80)}
.footer-links{left:0;top:1140px;width:1083px;text-align:center;font-family:"Open Sans",sans-serif;font-size:12.4px;color:#fff}
.footer-copy{left:0;top:1162px;width:1083px;text-align:center;font-family:"Open Sans",sans-serif;font-size:12.4px;color:#fff}
.social{left:879px;top:1150px;display:flex;gap:9px}
.social span{width:23px;height:23px;border-radius:2px;background:#6f96c4}
</style>
</head>
<body>
<div class="page">
  <div class="abs top-strip"></div>
  <header class="abs header"></header>
  <div class="abs brand">
    <div class="brand-mark"></div>
    <div class="brand-name">Torvell Biologics</div>
  </div>

  <div class="abs hero" role="img" aria-label="Stock photo of scientists in lab coats working at a laboratory bench with bottles and glassware"></div>
  <div class="abs slider-dots"><span class="active"></span><span></span><span></span></div>

  <nav class="abs nav">
    <span class="abs nav-item" style="left:100px">Home</span>
    <span class="abs nav-sep" style="left:161px"></span>
    <span class="abs nav-item" style="left:222px">Laboratory</span>
    <span class="abs nav-sep" style="left:284px"></span>
    <span class="abs nav-item" style="left:347px">Research</span>
    <span class="abs nav-sep" style="left:407px"></span>
    <span class="abs nav-item" style="left:467px">Team</span>
    <span class="abs nav-sep" style="left:530px"></span>
    <span class="abs nav-item" style="left:590px">Press</span>
    <span class="abs nav-sep" style="left:652px"></span>
    <span class="abs nav-item" style="left:712px">Contact us</span>
    <span class="abs nav-sep" style="left:775px"></span>
  </nav>
  <div class="abs search">Search
    <svg width="18" height="18" viewBox="0 0 18 18"><circle cx="7" cy="7" r="5" fill="none" stroke="#fff" stroke-width="2"/><line x1="11" y1="11" x2="16" y2="16" stroke="#fff" stroke-width="2.5" stroke-linecap="round"/></svg>
  </div>
  <div class="abs band"></div>

  <aside class="abs sidebar"></aside>

  <h1 class="abs welcome-title">WELCOME</h1>
  <h2 class="abs welcome-sub">TO OUR&nbsp; TORVELL BIOLOGICS, LLC</h2>
  <p class="abs text welcome-text">Pellentesque suscipit dictum eleifend. Ut urna diam, iaculis faucibus fringilla non, tincidunt ut dolor. Nulla ullamcorper porttitor tellus, in volutpat velit interdum id. Aliquam erat volutpat. Maecenas vel nulla nibh, sed accumsan ante. Mauris nec urna massa, a blandit nulla. Sed felis odio, tempus non dapibus vitae, placerat nec augue. Etiam molestie ligula eu odio commodo tempus. Phasellus ullamcorper libero sed felis tempor eu ullamcorper orci egestas. Etiam tempor mollis risus vel dapibus. Donec id nisl sed lectus ullamcorper pellentesque. Sed quis mi nisi. Integer volutpat tincidunt libero.</p>
  <div class="abs btn" style="left:571px;top:788px;width:126px">READ MORE</div>
  <div class="abs rule-h" style="left:36px;top:837px;width:670px"></div>

  <h3 class="abs section-title" style="left:29px;top:869px">FEATURED <span>SERVICES</span></h3>
  <ul class="abs services">
    <li>Etiam a odio et odio euismod placerat</li>
    <li>Maecenas adipiscing leo non turpis</li>
    <li>Praesent nec sem massa, et</li>
    <li>Nam tempus viverra magna, at volutpat</li>
    <li>Etiam a odio et odio euismod</li>
  </ul>
  <div class="abs btn" style="left:161px;top:1056px;width:126px">READ MORE</div>
  <div class="abs rule-v"></div>

  <h3 class="abs section-title" style="left:358px;top:869px">WHAT <span>WE DO</span></h3>
  <p class="abs text" style="left:358px;top:907px;width:338px">Etiam molestie ligula eu odio commodo tempus. Phasellus ullamcorper libero sed felis tempor eu ullamcorper orci egestas. Etiam tempor mollis risus vel dapibus. Donec id nisl sed lectus ullamcorper pellentesque. Sed quis mi nisi. Integer volutpat tincidunt libero. Etiam tempor mollis risus vel dapibus. Donec id nisl sed lectus ullamcorper pellentes­que. Sed quis mi nisi. Integer volutpat tincidunt libero.</p>
  <div class="abs btn" style="left:571px;top:1056px;width:126px">READ MORE</div>

  <h3 class="abs section-title" style="left:759px;top:613px">LATEST <span>NEWS</span></h3>
  <div class="abs news-date" style="left:759px;top:667px">10 feb 2012</div>
  <p class="abs text news-text" style="left:759px;top:690px">Etiam tempor mollis risus vel dapibus. Donec id nisl sed lectus ullamcorper pellentesque. Sed quis mi nisi.</p>
  <div class="abs btn" style="left:907px;top:759px;width:105px;height:26px;line-height:26px">READ MORE</div>
  <div class="abs rule-h" style="left:751px;top:801px;width:269px;background:#cfcfcf"></div>
  <div class="abs news-date" style="left:759px;top:822px">10 feb 2012</div>
  <p class="abs text news-text" style="left:759px;top:845px">Etiam tempor mollis risus vel dapibus. Donec id nisl sed lectus ullamcorper pellentesque. Sed quis mi nisi.</p>
  <div class="abs btn" style="left:907px;top:914px;width:105px;height:26px;line-height:26px">READ MORE</div>

  <div class="abs staff" role="img" aria-label="Photo of a staff scientist beside a microscope">
    <div class="abs staff-title">Our<br>Staff</div>
    <svg class="abs staff-arrow" width="30" height="30" viewBox="0 0 30 30"><circle cx="15" cy="15" r="13" fill="#f4f4f4" stroke="#555" stroke-width="2"/><path d="M11 8 L20 15 L11 22 Z" fill="#555"/></svg>
  </div>

  <footer class="abs footer"></footer>
  <div class="abs footer-links">Home | Laboratory | Research | Team | Press | Contact us</div>
  <div class="abs footer-copy">2012 © copyrights.torvellbiologics.received</div>
  <div class="abs social"><span></span><span></span><span></span><span></span><span></span></div>
</div>
</body>
</html>
```